Garlic Farm for Farm Sales/Restaurant sales

Need a professional, but appealing to agriculture world. We are selling 27 kinds of Organic Garlic from a farm in Simla,CO. I have uploaded logo and business information-we are going to need a template, because I will need to use it for four separate people.
-We are trying to appeal to Farm to table restaurants
-As well as growers/farmers

Target Market(s)

Agriculture Sales/Restaurants-Organic

Industry/Entity Type

Agriculture

Contact Information for Business Card

Want it to look more unique then your average kelto stock card- I want it to look amazing

Font styles to use
Sans Serif

Colors
0455a3
ec1f27
fbed22
ffffff

Requirements
Must have
• Just be creative
Nice to have
• Colorful
Should not have
• plain

```html
<!DOCTYPE html>
<html lang="en">
<head>
<meta charset="utf-8">
<title>Summit Ridge Gourmet Garlic — Business Card</title>
<link rel="stylesheet" href="https://fonts.googleapis.com/css2?family=Open+Sans:wght@400;600&display=swap">
<style>
  :root {
    --navy: #1b3566;
    --red: #c0092b;
    --red-soft: #d4434a;
    --yellow: #fdd800;
    --white: #ffffff;
    --ink: #5a5a5a;
    --rule: #8a8a8a;
    --backdrop: #ebe6e1;
  }
  * { margin: 0; padding: 0; box-sizing: border-box; }
  html, body { width: 1200px; height: 987px; overflow: hidden; }
  body {
    background: var(--backdrop);
    font-family: "Open Sans", Arial, sans-serif;
    position: relative;
  }
  .card {
    position: absolute;
    left: 293px;
    width: 615px;
    height: 350px;
    overflow: hidden;
  }
  .card--front { top: 130px; background: var(--white); }
  .card--back { top: 506px; background: var(--red); }

  /* front */
  .brand-emblem {
    position: absolute;
    left: 434px; top: 37px;
    width: 92px; height: 92px;
    border-radius: 50%;
    background: radial-gradient(circle at 50% 50%, var(--yellow) 0 38%, var(--red) 62%);
  }
  .brand-name {
    position: absolute;
    right: 30px; top: 134px;
    text-align: right;
    font-weight: 600;
    color: var(--navy);
    white-space: nowrap;
    line-height: 1.1;
  }
  .brand-name .brand-main { display: block; font-size: 26px; }
  .brand-name .brand-sub { display: block; font-size: 13px; letter-spacing: 0.5px; }
  .name-tab {
    position: absolute;
    left: -14px; top: 189px;
    width: 28px; height: 54px;
    border-radius: 50%;
    background: var(--red);
  }
  .person-name {
    position: absolute;
    left: 35px; top: 194px;
    font-size: 21px;
    font-weight: 600;
    color: var(--navy);
    letter-spacing: 0.3px;
  }
  .person-role {
    position: absolute;
    left: 35px; top: 222px;
    font-size: 15px;
    color: var(--red);
  }
  .divider {
    position: absolute;
    left: 35px; top: 249px;
    width: 550px; height: 1px;
    background: var(--rule);
  }
  .contact-list {
    position: absolute;
    left: 35px; top: 259px;
    list-style: none;
  }
  .contact-list li {
    display: flex;
    align-items: center;
    height: 23.5px;
    font-size: 15px;
    color: var(--ink);
  }
  .contact-list svg { width: 14px; height: 14px; margin-right: 8px; fill: var(--navy); }
  .address {
    position: absolute;
    right: 30px; top: 282px;
    text-align: right;
    font-size: 15px;
    line-height: 23.5px;
    color: var(--ink);
  }

  /* back */
  .back-emblem {
    position: absolute;
    left: 270px; top: 8px;
    width: 334px; height: 334px;
    border-radius: 50%;
    background: radial-gradient(circle at 52% 50%, var(--yellow) 0 42%, #f0a21a 56%, var(--red-soft) 72%);
  }
  .back-brand {
    position: absolute;
    left: 14px; top: 236px;
    text-align: right;
    font-weight: 600;
    color: var(--white);
    white-space: nowrap;
    line-height: 1.1;
  }
  .back-brand .brand-main { display: block; font-size: 32px; }
  .back-brand .brand-sub { display: block; font-size: 15px; letter-spacing: 0.5px; }
  .social-row {
    position: absolute;
    left: 90px; top: 312px;
    display: flex;
    gap: 4px;
  }
  .social-row span {
    width: 20px; height: 20px;
    border-radius: 50%;
    border: 1.5px solid var(--white);
  }
</style>
</head>
<body>
  <section class="card card--front" aria-label="Card front">
    <div class="brand-emblem" role="img" aria-label="Brand emblem area"></div>
    <p class="brand-name"><span class="brand-main">Summit Ridge</span><span class="brand-sub">gourmet garlic</span></p>
    <div class="name-tab"></div>
    <h1 class="person-name">DALE PORTER</h1>
    <p class="person-role">CEO/FOUNDER</p>
    <div class="divider"></div>
    <ul class="contact-list">
      <li><svg viewBox="0 0 24 24"><path d="M6.6 10.8a15.1 15.1 0 0 0 6.6 6.6l2.2-2.2a1 1 0 0 1 1-.25 11.4 11.4 0 0 0 3.6.57 1 1 0 0 1 1 1V20a1 1 0 0 1-1 1A17 17 0 0 1 3 4a1 1 0 0 1 1-1h3.5a1 1 0 0 1 1 1c0 1.25.2 2.45.57 3.57a1 1 0 0 1-.25 1z"/></svg>555-014-2276</li>
      <li><svg viewBox="0 0 24 24"><path d="M2 5h20v2l-10 6L2 7zM2 9l10 6 10-6v10H2z"/></svg>dale@SRGarlic.com</li>
      <li><svg viewBox="0 0 24 24"><circle cx="12" cy="12" r="10"/></svg>www.SRGarlic.com</li>
    </ul>
    <p class="address">P.O. Box 48 Fernly<br>CO&nbsp; 80911</p>
  </section>

  <section class="card card--back" aria-label="Card back">
    <div class="back-emblem" role="img" aria-label="Large brand emblem with golden garlic bulb"></div>
    <p class="back-brand"><span class="brand-main">Summit Ridge</span><span class="brand-sub">gourmet garlic</span></p>
    <div class="social-row" aria-label="Social links">
      <span></span><span></span><span></span><span></span>
    </div>
  </section>
</body>
</html>
```